General contractor/GM consaltant business card

I need a card for my contracting company in North Dakota, we build industrial buildings for the oil feild and oil feild related companies offices, shops, airplain hangars, airports ext. We have a familly atmosphere on the job and are very relational and personal.
Industry/Entity Type
Industrial
Contact Information for Business Card
Ridgepost Contractors LLC.
Derek T.Holloway
4837 Tamarind dr. Colorado Springs, CO. 80917
Cell# 406-555-0148
derek@ridgepostcontractors.com

```html
<!DOCTYPE html>
<html lang="en">
<head>
<meta charset="utf-8">
<title>Ridgepost Contractors LLC. — Business Card</title>
<link rel="stylesheet" href="https://fonts.googleapis.com/css2?family=Philosopher:wght@700&family=Arimo:wght@400&display=swap">
<style>
  :root {
    --backdrop: #e9e7e3;
    --card: #fbfbfb;
    --brand-red: #e0262f;
    --band-blue: #2a62b5;
    --text-grey: #5a5d63;
  }
  * { box-sizing: border-box; margin: 0; padding: 0; }
  html, body {
    width: 1200px; height: 858px; overflow: hidden;
    background: var(--backdrop);
  }
  .canvas {
    width: 1200px; height: 858px;
    display: flex; align-items: center; justify-content: center; gap: 40px;
  }
  .card {
    position: relative;
    width: 560px; height: 320px;
    background: var(--card);
    box-shadow: 0 2px 8px rgba(0,0,0,0.15);
    overflow: hidden;
  }
  .wordmark {
    font-family: "Philosopher", serif;
    font-weight: 700;
    color: var(--brand-red);
    white-space: nowrap;
  }
  .card-front .wordmark {
    position: absolute; left: 56px; top: 60px;
    font-size: 34px;
  }
  .card-front .holder-name {
    position: absolute; left: 210px; top: 128px;
    font-family: "Arimo", sans-serif;
    font-size: 18px;
    color: var(--brand-red);
  }
  .band {
    position: absolute; left: 0; right: 0; top: 156px;
    height: 30px;
    background: var(--band-blue);
  }
  .contact-list {
    position: absolute; left: 56px; top: 206px;
    list-style: none;
    font-family: "Arimo", sans-serif;
    font-size: 14px;
    color: var(--text-grey);
  }
  .contact-list li {
    display: flex; align-items: center; gap: 12px;
    height: 26px;
  }
  .contact-list svg { width: 14px; height: 14px; fill: var(--brand-red); flex: none; }
  .card-back {
    display: flex; align-items: center; justify-content: center;
  }
  .card-back .wordmark { font-size: 40px; }
</style>
</head>
<body>
<main class="canvas">
  <section class="card card-front" aria-label="Card front">
    <div class="wordmark">Ridgepost Contractors LLC.</div>
    <div class="holder-name">Derek T.Holloway</div>
    <div class="band"></div>
    <ul class="contact-list">
      <li>
        <svg viewBox="0 0 16 16" aria-hidden="true"><path d="M3 2h3l1.5 3.5-2 1.3a8 8 0 0 0 3.7 3.7l1.3-2L14 10v3a1 1 0 0 1-1 1A11 11 0 0 1 2 3a1 1 0 0 1 1-1z"/></svg>
        <span>406-555-0148</span>
      </li>
      <li>
        <svg viewBox="0 0 16 16" aria-hidden="true"><path d="M8 1a5 5 0 0 0-5 5c0 4 5 9 5 9s5-5 5-9a5 5 0 0 0-5-5zm0 7a2 2 0 1 1 0-4 2 2 0 0 1 0 4z"/></svg>
        <span>4837 Tamarind dr. Colorado Springs, CO. 80917</span>
      </li>
      <li>
        <svg viewBox="0 0 16 16" aria-hidden="true"><path d="M1 3h14v10H1zM2 4.2V5l6 4 6-4v-.8L8 8z"/></svg>
        <span>derek@ridgepostcontractors.com</span>
      </li>
    </ul>
  </section>

  <section class="card card-back" aria-label="Card back">
    <div class="wordmark">Ridgepost Contractors LLC.</div>
  </section>
</main>
</body>
</html>
```